KAJU Freightways #ALLKAJU Business Cards & Letterhead

I am looking to business cards designed for our organization. We are currently undergoing a small re-branding that is taking place. Our organization is called KAJU Freightways and we are headquartered in Phoenix, AZ. We primarily provide transportation and logistics services to the Marlow Parcel Bureau who is our largest customer. I would like to see a design that incorporates name, title, contact info, website, and address (this will be different depending on the employee). I would also like to see some color on the business card using our logo colors or a variation. I would like our logo on the back of the business card with the website displayed. The final design should communicate that we are a next generation transportation operate that focuses on being driver-first, customer-centric, innovative, and sustainable.We would also like our #ALLKAJU catch phrase incorporated as well.

Target Market(s)

Transportation & Logistics

Industry/Entity Type

Trucking Company

Contact Information for Business Card

-First and Last Name
-Position Title
-Contact Phone
-Contact Email
-Physical Address

Font styles to use
Serif

Colors

Designer to choose colors to be used in the design.

Requirements
Must have
• -KAJU logo prominently displayed
• -#ALLKAJU catch phrase used
• -Some amount of color, design gradient, etc.
• -Logo on the back with website listed (https://www.kajufreightco.example)

```html
<!DOCTYPE html>
<html lang="en">
<head>
<meta charset="utf-8">
<title>KAJU Freightways Business Card</title>
<link rel="stylesheet" href="https://fonts.googleapis.com/css2?family=Roboto+Slab:wght@400;500;800&display=swap">
<style>
  :root {
    --teal: #1d4652;
    --teal-deep: #163a44;
    --green: #7cc242;
    --white: #ffffff;
    --ink: #1f4450;
    --rule: #9aa8ad;
    --backdrop: #3a3431;
  }
  * { margin: 0; padding: 0; box-sizing: border-box; }
  html, body {
    width: 1200px; height: 716px; overflow: hidden;
    background: var(--backdrop);
    font-family: "Roboto Slab", serif;
  }
  .canvas { position: relative; width: 1200px; height: 716px; }
  .card {
    position: absolute; top: 204px;
    width: 540px; height: 309px;
    overflow: hidden;
  }

  /* Back */
  .card-back {
    left: 40px; background: var(--teal);
    border-bottom: 4px solid var(--green);
    display: flex; flex-direction: column; align-items: center; justify-content: center;
  }
  .brand {
    display: flex; align-items: center; gap: 12px;
    font-weight: 800; letter-spacing: 2px; line-height: 1;
  }
  .brand-dot { border-radius: 50%; background: var(--green); flex: none; }
  .card-back .brand { font-size: 58px; color: var(--white); }
  .card-back .brand-dot { width: 22px; height: 22px; }
  .back-url {
    margin-top: 28px;
    color: var(--white); font-size: 15px; letter-spacing: 1.2px;
  }
  .tagline {
    margin-top: 8px;
    color: var(--green); font-size: 14px; font-weight: 500; letter-spacing: 2px;
  }

  /* Front */
  .card-front { left: 620px; background: var(--white); }
  .waves { position: absolute; inset: 0; width: 540px; height: 309px; }
  .card-front .brand { position: absolute; left: 34px; top: 62px; font-size: 48px; color: var(--ink); }
  .card-front .brand-dot { width: 18px; height: 18px; }

  .person { position: absolute; right: 30px; top: 30px; text-align: right; }
  .person-name { color: var(--green); font-size: 22px; font-weight: 500; letter-spacing: 1px; }
  .person-title { color: var(--ink); font-size: 14px; margin-top: 2px; }
  .person-rule { width: 36px; height: 1px; background: var(--rule); margin: 8px 0 8px auto; }
  .address { color: var(--ink); font-size: 12.5px; line-height: 1.45; font-style: normal; }

  .contacts {
    position: absolute; right: 22px; bottom: 16px;
    list-style: none; color: var(--white);
    font-size: 14px; line-height: 1.5;
  }
  .contacts li { display: flex; justify-content: flex-end; align-items: center; gap: 10px; }
  .contacts .hl { color: var(--green); }
  .icon { width: 12px; height: 12px; flex: none; }
</style>
</head>
<body>
<main class="canvas">
  <section class="card card-back" aria-label="Card back">
    <div class="brand"><span class="brand-dot"></span>KAJU</div>
    <p class="back-url">www.kajufreightco.example</p>
    <p class="tagline">#ALLKAJU</p>
  </section>

  <section class="card card-front" aria-label="Card front">
    <svg class="waves" viewBox="0 0 540 309" aria-hidden="true">
      <path d="M0,140 C40,190 120,212 240,214 C330,216 420,190 540,160 L540,309 L0,309 Z" fill="var(--green)"/>
      <path d="M0,156 C60,200 150,222 260,220 C360,218 440,188 540,166 L540,309 L0,309 Z" fill="var(--white)"/>
      <path d="M60,145 C120,195 220,212 320,205 C410,198 480,175 540,150 L540,166 C470,186 400,206 310,211 C210,215 120,196 60,145 Z" fill="var(--teal-deep)"/>
      <path d="M0,170 C80,215 170,226 280,222 C380,218 460,195 540,175 L540,309 L0,309 Z" fill="var(--teal)"/>
    </svg>
    <div class="brand"><span class="brand-dot"></span>KAJU</div>
    <div class="person">
      <p class="person-name">DARREN OKAFOR</p>
      <p class="person-title">Director</p>
      <div class="person-rule"></div>
      <address class="address">4410 North Cedar Ridge Road<br>Glendale, AZ 85301</address>
    </div>
    <ul class="contacts">
      <li>555-014-2290
        <svg class="icon" viewBox="0 0 12 12"><path d="M3 1 L5 3.5 L4 5 C5 7 6 8 7.5 8.5 L9 7.5 L11 9.5 L9.5 11 C5 10.5 1.5 7 1 2.5 Z" fill="var(--green)"/></svg></li>
      <li>info@kajufreightco.example
        <svg class="icon" viewBox="0 0 12 12"><rect x="1" y="2.5" width="10" height="7" fill="none" stroke="var(--green)" stroke-width="1.2"/><path d="M1 2.5 L6 7 L11 2.5" fill="none" stroke="var(--green)" stroke-width="1.2"/></svg></li>
      <li><span>www.<span class="hl">kajufreightco</span>.example</span>
        <svg class="icon" viewBox="0 0 12 12"><circle cx="6" cy="6" r="5" fill="none" stroke="var(--green)" stroke-width="1.2"/><path d="M1 6 H11 M6 1 C3 4 3 8 6 11 M6 1 C9 4 9 8 6 11" fill="none" stroke="var(--green)" stroke-width="1"/></svg></li>
    </ul>
  </section>
</main>
</body>
</html>
```